Graphics for Verdaxa telehealth weight loss plans

Verdaxa focuses on delivering medical weight-loss using prescription medicine and telehealth consults. Verdaxa needs graphics for its ecommerce site for three weight loss plans. The plans are posted here with current graphics and descriptions of what is included with each plan. Please do not feel constrained by current graphics or styling.

- https://store.verdaxahealth.com/products/radiant-horizon-plan
- https://store.verdaxahealth.com/products/medication-kickstart-plan
- https://store.verdaxahealth.com/products/balanced-ascent-plan

The graphics need to look good on mobile and desktop browsers.

```html
<!DOCTYPE html>
<html lang="en">
<head>
<meta charset="utf-8">
<title>Verdaxa Weight Loss Plans</title>
<link href="https://fonts.googleapis.com/css2?family=Oswald:wght@300;400;500;600;700&display=swap" rel="stylesheet">
<style>
  :root {
    --sky: #29cdfc;
    --navy: #25205b;
    --royal: #2c4ea0;
    --white: #ffffff;
    --photo-light: #b9b9b9;
    --photo-dark: #5e5e5e;
    --page: #ffffff;
  }
  * { box-sizing: border-box; margin: 0; padding: 0; }
  html, body {
    width: 1200px; height: 521px; overflow: hidden;
    background: var(--page);
    font-family: "Oswald", "Arial Narrow", sans-serif;
  }
  .plans { position: relative; width: 1200px; height: 521px; }
  .plan {
    position: absolute; top: 13px; width: 383px; height: 495px; overflow: hidden;
  }
  .plan--kickstart { left: 13px; background: var(--sky); color: var(--navy); }
  .plan--balanced { left: 409px; background: var(--navy); color: var(--sky); }
  .plan--radiant { left: 804px; background: var(--royal); color: var(--white); }

  .plan__photo { position: absolute; left: 0; top: 0; width: 383px; height: 158px; }

  .plan__title {
    position: absolute; left: 26px; top: 118px;
    font-weight: 600; font-size: 45px; line-height: 44px; letter-spacing: 0.2px;
    text-transform: uppercase;
  }
  .plan--balanced .plan__title { left: 25px; font-weight: 500; }
  .plan--radiant .plan__title { left: 25px; top: 121px; }

  .plan__program {
    position: absolute; left: 26px; top: 207px;
    font-weight: 300; font-size: 20px; line-height: 24px; text-transform: uppercase;
  }
  .plan--radiant .plan__program { left: 29px; top: 211px; }

  .badge {
    position: absolute; height: 21px; padding: 0 8px;
    font-weight: 500; font-size: 14px; line-height: 21px;
  }
  .plan--kickstart .badge { left: 26px; top: 264px; background: var(--navy); color: var(--white); }
  .plan--balanced .badge { left: 26px; top: 215px; background: var(--sky); color: var(--navy); }
  .plan--radiant .badge { left: 30px; top: 269px; background: var(--white); color: var(--navy); }

  .features { list-style: none; }
  .feature {
    position: absolute; padding-left: 9px;
    font-weight: 500; font-size: 15px; line-height: 17.5px;
  }
  .feature::before { content: "•"; position: absolute; left: 0; top: 0; }
  .feature small { font-weight: 300; font-size: 11.5px; }
  .feature .note { display: block; font-weight: 300; font-size: 11.5px; line-height: 16px; }
  .plan--balanced .feature { font-size: 14.5px; }
  .plan--balanced .feature small { font-size: 12px; margin-left: 4px; }

  .disclaimer {
    position: absolute; left: 25px; top: 373px;
    font-weight: 300; font-size: 12.5px;
  }

  .billing { position: absolute; left: 25px; top: 422px; width: 230px; height: 44px; }
  .billing__bar {
    position: absolute; left: 32px; top: 13px; height: 20px; padding: 0 12px 0 20px;
    font-weight: 400; font-size: 14px; line-height: 20px; white-space: nowrap;
  }
  .billing__icon { position: absolute; left: 0; top: 0; width: 44px; height: 44px; }
  .plan--kickstart .billing__bar { background: var(--navy); color: var(--white); }
  .plan--balanced .billing__bar { background: var(--sky); color: var(--navy); }
  .plan--radiant .billing__bar { background: var(--white); color: var(--navy); }
</style>
</head>
<body>
<main class="plans">

  <!-- Medication Kickstart Plan -->
  <section class="plan plan--kickstart">
    <svg class="plan__photo" viewBox="0 0 383 158" role="img" aria-label="Black and white photo of a tape measure around a waist beside scattered capsules">
      <defs>
        <linearGradient id="photoA" x1="0" y1="0" x2="1" y2="0.4">
          <stop offset="0" stop-color="#6a6a6a"/>
          <stop offset="0.5" stop-color="#c4c4c4"/>
          <stop offset="1" stop-color="#8a8a8a"/>
        </linearGradient>
      </defs>
      <path d="M0 0H383V158H294V109H0Z" fill="url(#photoA)"/>
    </svg>
    <h2 class="plan__title">Medication<br>Kickstart Plan</h2>
    <p class="plan__program">Physician Consultation<br>Phentermine Program</p>
    <span class="badge">Includes</span>
    <ul class="features">
      <li class="feature" style="left:23px;top:296px">100% online.<span class="note">No need to visit the office.</span></li>
      <li class="feature" style="left:23px;top:334px">Phentermine<br>prescription.</li>
      <li class="feature" style="left:23px;top:374px">Medical<br>consultation.</li>
      <li class="feature" style="left:175px;top:293px">Real Phentermine <small>(37.5mg/Pill)</small><br>delivered to your door.</li>
      <li class="feature" style="left:175px;top:342px">1 month supply. <small>(30 pills)</small></li>
      <li class="feature" style="left:175px;top:372px">FREE Introductory Nutritionist<br>consult on your first month.</li>
    </ul>
    <div class="billing">
      <span class="billing__bar">Month-to-month pay as you go.</span>
      <svg class="billing__icon" viewBox="0 0 44 44" aria-hidden="true">
        <circle cx="22" cy="22" r="22" fill="var(--navy)"/>
        <g fill="none" stroke="var(--white)" stroke-width="1.4">
          <ellipse cx="22" cy="17" rx="10" ry="4.5"/>
          <path d="M12 17v4c0 2.5 4.5 4.5 10 4.5s10-2 10-4.5v-4"/>
          <path d="M20 14.5l3.5 5M22 13.5v7"/>
          <path d="M31 26c-2 4-6 6-11 5.5M15 29l-3 2 3.5 1.5"/>
        </g>
      </svg>
    </div>
  </section>

  <!-- Balanced Ascent Plan -->
  <section class="plan plan--balanced">
    <svg class="plan__photo" viewBox="0 0 383 158" role="img" aria-label="Black and white photo of a woman in a sports top holding a protein shaker in a kitchen">
      <defs>
        <linearGradient id="photoB" x1="0" y1="0" x2="1" y2="0.3">
          <stop offset="0" stop-color="#7a7a7a"/>
          <stop offset="0.45" stop-color="#bdbdbd"/>
          <stop offset="1" stop-color="#9a9a9a"/>
        </linearGradient>
      </defs>
      <path d="M0 0H383V158H281V109H0Z" fill="url(#photoB)"/>
    </svg>
    <h2 class="plan__title">Balanced<br>Ascent Plan</h2>
    <span class="badge">Includes</span>
    <ul class="features">
      <li class="feature" style="left:22px;top:259px">100% online.<small>No need to visit the office.</small></li>
      <li class="feature" style="left:22px;top:287px">Expert nutrition consult.</li>
      <li class="feature" style="left:22px;top:317px">Custom crafted diet plan to achieve your goals.</li>
      <li class="feature" style="left:22px;top:347px">Nutrition coaching to improve your health and vitality.</li>
    </ul>
    <p class="disclaimer">*Does not include medication</p>
    <div class="billing" style="left:29px">
      <span class="billing__bar">Month-to-month pay as you go.</span>
      <svg class="billing__icon" viewBox="0 0 44 44" aria-hidden="true">
        <circle cx="22" cy="22" r="22" fill="var(--sky)"/>
        <g fill="none" stroke="var(--navy)" stroke-width="1.4">
          <ellipse cx="22" cy="17" rx="10" ry="4.5"/>
          <path d="M12 17v4c0 2.5 4.5 4.5 10 4.5s10-2 10-4.5v-4"/>
          <path d="M20 14.5l3.5 5M22 13.5v7"/>
          <path d="M31 26c-2 4-6 6-11 5.5M15 29l-3 2 3.5 1.5"/>
        </g>
      </svg>
    </div>
  </section>

  <!-- Radiant Horizon Plan -->
  <section class="plan plan--radiant">
    <svg class="plan__photo" viewBox="0 0 383 158" role="img" aria-label="Black and white photo of a muscular torso beside scattered capsules">
      <defs>
        <linearGradient id="photoC" x1="0" y1="0" x2="1" y2="0.4">
          <stop offset="0" stop-color="#8c8c8c"/>
          <stop offset="0.4" stop-color="#5f5f5f"/>
          <stop offset="1" stop-color="#c2c2c2"/>
        </linearGradient>
      </defs>
      <path d="M0 0H383V158H294V109H0Z" fill="url(#photoC)"/>
    </svg>
    <h2 class="plan__title">Radiant<br>Horizon Plan</h2>
    <p class="plan__program">Physician Consultation<br>Phentermine Program</p>
    <span class="badge">Includes</span>
    <ul class="features">
      <li class="feature" style="left:21px;top:304px">100% online.<span class="note" style="margin-left:4px;margin-top:3px">No need to visit the office.</span></li>
      <li class="feature" style="left:24px;top:345px">1 month supply. <small>(30 pills)</small></li>
      <li class="feature" style="left:21px;top:369px">Custom crafted diet plan<br>to achieve your goals.</li>
      <li class="feature" style="left:183px;top:302px">Real Phentermine <small>(37.5mg/Pill)</small><br>delivered to your door.</li>
      <li class="feature" style="left:185px;top:345px">Expert nutrition consult.</li>
      <li class="feature" style="left:183px;top:369px">Nutrition coaching to improve<br>your health and vitality.</li>
    </ul>
    <div class="billing" style="left:25px">
      <span class="billing__bar">Month-to-month pay as you go.</span>
      <svg class="billing__icon" viewBox="0 0 44 44" aria-hidden="true">
        <circle cx="22" cy="22" r="22" fill="var(--white)"/>
        <g fill="none" stroke="var(--navy)" stroke-width="1.4">
          <ellipse cx="22" cy="17" rx="10" ry="4.5"/>
          <path d="M12 17v4c0 2.5 4.5 4.5 10 4.5s10-2 10-4.5v-4"/>
          <path d="M20 14.5l3.5 5M22 13.5v7"/>
          <path d="M31 26c-2 4-6 6-11 5.5M15 29l-3 2 3.5 1.5"/>
        </g>
      </svg>
    </div>
  </section>

</main>
</body>
</html>
```